Modern Business Card for Larkwell 2018

Our company assumes the best about people. We are creating an online community of entrepreneurs and business leaders who struggle with marketing their business online.

This business card should POP! We recently got a new logo and are launching a new website next month, so our business cards should make a statement that feels:
-Fresh
-Smart
-Trustworthy
-Fun

Target Market(s)

small business owners, entrepreneurs

Industry/Entity Type

Digital Marketing

Contact Information for Business Card

Dimensions: 3.5" x 2"

Font styles to use
Sans Serif

Colors
f37122
ffffff

Requirements
Must have
• We need a business card with a modern, bold design. We will use one side of the card as a lead-generation offer, so text on one side will need to fit up to 140 characters. The business card should stick to our core colors (orange, black, and white).
Nice to have
• We think a vertical "portrait" design could be interesting.
Should not have
• Should not look like a traditional business card. The round icon should stand out from a distance.

```html
<!DOCTYPE html>
<html lang="en">
<head>
<meta charset="utf-8">
<title>Larkwell Business Card</title>
<link rel="stylesheet" href="https://fonts.googleapis.com/css2?family=Roboto:wght@400;500;700&family=Montserrat:wght@700&family=Great+Vibes&family=Permanent+Marker&display=swap">
<style>
  :root {
    --orange: #e8662a;
    --black: #1b1c1d;
    --white: #f4f4f4;
    --paper: #ffffff;
    --backdrop: #e2e2e2;
    --rule: #7d7d7d;
    --ink: #222222;
  }
  * { margin: 0; padding: 0; box-sizing: border-box; }
  html, body { width: 1200px; height: 960px; overflow: hidden; }
  body {
    position: relative;
    background: var(--backdrop);
    font-family: "Roboto", Arial, sans-serif;
  }
  .card {
    position: absolute;
    width: 343px;
    height: 600px;
    overflow: hidden;
  }
  /* Front */
  .card-front {
    left: 234px; top: 179px;
    background: var(--paper);
  }
  .front-name {
    position: absolute;
    left: 171px; top: 232px;
    transform: translate(-50%, -50%) rotate(-90deg);
    white-space: nowrap;
    font-family: "Great Vibes", cursive;
    font-size: 64px;
    color: var(--orange);
    line-height: 1;
  }
  .front-role {
    position: absolute;
    top: 435px; width: 100%;
    text-align: center;
    font-weight: 500;
    font-size: 19px;
    color: var(--ink);
    letter-spacing: 0.2px;
  }
  .front-email {
    position: absolute;
    top: 459px; width: 100%;
    text-align: center;
    font-size: 14px;
    color: var(--ink);
  }
  .front-brand {
    position: absolute;
    top: 492px; width: 100%;
    display: flex; align-items: center; justify-content: center;
    gap: 8px;
    font-weight: 700;
    font-size: 20px;
    color: var(--orange);
  }
  .brand-dot {
    width: 44px; height: 44px;
    border-radius: 50%;
    background: var(--orange);
  }
  /* Back */
  .card-back {
    left: 623px; top: 182px;
    background: var(--black);
  }
  .back-header {
    position: absolute;
    top: 0; left: 0; width: 100%; height: 171px;
    text-align: center;
  }
  .header-dot {
    position: absolute;
    left: 152px; top: 30px;
    width: 40px; height: 40px;
    border-radius: 50%;
    background: var(--orange);
  }
  .header-name {
    position: absolute;
    top: 84px; width: 100%;
    font-family: "Montserrat", Arial, sans-serif;
    font-weight: 700;
    font-size: 36px;
    color: var(--white);
    letter-spacing: 1px;
    line-height: 1;
  }
  .header-tagline {
    position: absolute;
    top: 124px; width: 100%;
    font-family: "Permanent Marker", "Roboto", sans-serif;
    font-size: 11.5px;
    line-height: 14px;
    color: var(--white);
    letter-spacing: 0.6px;
  }
  .offer-band {
    position: absolute;
    top: 171px; left: 0; width: 100%; height: 281px;
    background: var(--orange);
    text-align: center;
    color: var(--white);
  }
  .offer-headline {
    margin-top: 28px;
    font-weight: 700;
    font-size: 20.5px;
    line-height: 24px;
    letter-spacing: 0.2px;
  }
  .offer-copy {
    margin-top: 8px;
    font-size: 14.5px;
    line-height: 18px;
  }
  .offer-link {
    margin-top: 14px;
    font-weight: 700;
    font-size: 19px;
  }
  .notes-panel {
    position: absolute;
    left: 25px; top: 398px;
    width: 291px; height: 220px;
    background: var(--white);
    border-radius: 14px 14px 0 0;
  }
  .note-line {
    position: absolute;
    left: 20px; right: 20px;
    height: 2px;
    background: var(--rule);
  }
</style>
</head>
<body>
  <section class="card card-front">
    <div class="front-name">Dana Morrow</div>
    <div class="front-role">STORY MARKETING COACH</div>
    <div class="front-email">dana@larkwellnow.com</div>
    <div class="front-brand"><span class="brand-dot"></span>Larkwell</div>
  </section>

  <section class="card card-back">
    <header class="back-header">
      <span class="header-dot"></span>
      <div class="header-name">LARKWELL</div>
      <div class="header-tagline">SHARE IDEAS THAT SPARK PROGRESS</div>
    </header>
    <div class="offer-band">
      <p class="offer-headline">GROW YOUR AUDIENCE.<br>EARN MORE REVENUE.<br>BUILD LASTING VALUE.</p>
      <p class="offer-copy">Get your free Larkwell<br>Starter Package and our<br>marketing guide today at</p>
      <p class="offer-link">Larkwellnow.com/start</p>
    </div>
    <div class="notes-panel">
      <span class="note-line" style="top:44px"></span>
      <span class="note-line" style="top:83px"></span>
      <span class="note-line" style="top:121px"></span>
      <span class="note-line" style="top:159px"></span>
    </div>
  </section>
</body>
</html>
```